Unique Builder wordpress website - Supply Graphics Only

We need a brand new website for a building company in Perth, Australia who constructs insulated panels (sip).
What is a SIP?
A SIP is a high-performance building panel used for floors, walls, and roofs in residential and commercial buildings. Panels are typically made using Expanded Polystyrene (EPS) sandwiched between two structural skins.
The design must incorporate a slick professional look and keep to the logo colours (Lime green & Blacks). The logo must not change colours or be altered. (
We will convert the graphics to a wordpress site. We have our own coders)
Design:
The website design must be clean, mobile friendly and the final design will be adapted to WordPress CMS.
The menus must contain dropdown menus and front page may contain a youtube video at a later date.
Fonts must be clear and easy to read
The contact us page will need to have an online form and google map.
The 16 pages listed will be the complete site and are for reference only. For this project the winning designer would need to supply the Homepage, and 1 inner pages only as PSD files.
The structure is as follows:
Home
About us
Marlow Fen Dwellings
What is a sip
Benefits
FAQ
Designs
Residential
Granny Flats
Architectural design
Photo Gallery <--- Would be great if a sample design can be provided
Services
Project management and custom design
Site Assembly
Kit Supply
Contact us
***We don't need the designer to design every page however a 1 inner page would be ideal****
Our Competitors websites
Note: the following websites look crap however, the following websites are some of our competitors. We want a clean and awesome layout.
http://www.corvamoda.com.au/
http://dralventorix.com.au/
http://www.quilbarrow.net.au/
New home builders and commercial builders
Building
5+ page

```html
<!DOCTYPE html>
<html lang="en">
<head>
<meta charset="utf-8">
<title>Panelvance – Home</title>
<link href="https://fonts.googleapis.com/css2?family=Montserrat:wght@600;700&family=Open+Sans:ital,wght@0,400;0,600;0,700;1,400&display=swap" rel="stylesheet">
<style>
:root{
  --lime:#a3c93a;
  --lime-dark:#8db22b;
  --ink:#333333;
  --text:#6b6b6b;
  --muted:#8a8a8a;
  --night:#2a2a2a;
  --footer:#1f1f1f;
  --pale:#f4f4f6;
  --card:#f6f6f6;
  --amber:#f6b90f;
  --steel:#5b5b5b;
  --white:#ffffff;
}
*{margin:0;padding:0;box-sizing:border-box}
html,body{width:1200px;height:2517px;overflow:hidden}
body{position:relative;background:var(--white);font-family:"Open Sans",Arial,sans-serif;color:var(--text)}
.abs{position:absolute}

/* header */
.topline{left:0;top:0;width:1200px;height:4px;background:var(--lime)}
.header{left:0;top:4px;width:1200px;height:96px;background:var(--white)}
.brand{left:84px;top:32px;display:flex;align-items:center;gap:12px}
.brand-mark{width:32px;height:32px;background:var(--lime)}
.brand-name{font-family:"Open Sans",Arial,sans-serif;font-weight:700;font-size:32px;color:var(--ink);letter-spacing:-0.5px;white-space:nowrap}
.main-nav{left:398px;top:4px;height:96px;display:flex;align-items:stretch}
.main-nav a{display:flex;align-items:center;padding:0 15px;font-size:12.5px;color:#7a7a7a;text-decoration:none;text-transform:uppercase;letter-spacing:.3px;white-space:nowrap}
.main-nav a.active{background:var(--lime);color:var(--white);padding:0 18px}
.sub-nav{left:0;top:100px;width:1200px;height:54px;background:var(--night);border-bottom:4px solid var(--lime);display:flex;align-items:center;justify-content:space-between;padding:0 100px}
.sub-nav a{color:var(--white);font-size:12px;text-decoration:none;text-transform:uppercase;white-space:nowrap;letter-spacing:.1px}

/* hero */
.hero{left:0;top:158px;width:1200px;height:468px;background:linear-gradient(135deg,#3b3027 0%,#6b5237 35%,#7a5c3a 55%,#3d342c 100%)}
.hero-shade{left:0;top:0;width:100%;height:100%;background:rgba(20,20,20,.38)}
.hero-title{left:0;top:136px;width:1200px;text-align:center;font-family:"Montserrat",Arial,sans-serif;font-weight:700;font-size:62px;color:var(--lime);letter-spacing:2px;white-space:nowrap}
.hero-text{left:270px;top:218px;width:660px;text-align:center;font-style:italic;font-size:12px;line-height:21.5px;color:var(--white)}
.hero-btn{left:485px;top:313px;width:230px;height:44px;border:2px solid var(--lime);color:var(--lime);font-size:13px;display:flex;align-items:center;justify-content:center;text-transform:uppercase}
.dots{left:556px;top:436px;display:flex;gap:6px}
.dots span{width:13px;height:13px;border-radius:50%;border:2px solid var(--white)}
.dots span.on{border-color:var(--lime)}

/* section headings */
.sec-head{left:0;width:1200px;display:flex;justify-content:center;align-items:center;gap:14px;font-family:"Montserrat",Arial,sans-serif;font-weight:700;font-size:25px;text-transform:uppercase}
.sec-head .mark{width:24px;height:24px;background:var(--ink)}
.sec-head .hl{color:var(--lime)}
.sec-head .rest{color:var(--ink)}
.sec-intro{left:240px;width:720px;text-align:center;font-size:12px;line-height:22px;color:var(--muted)}

/* project cards */
.card{top:765px;width:316px;height:418px;background:var(--card);border:1px solid #e4e4e4;text-align:center}
.card-img{width:100%;height:201px}
.card h3{margin-top:22px;font-weight:400;font-size:18px;color:var(--ink);text-transform:uppercase;letter-spacing:.3px}
.card p{margin:16px auto 0;width:270px;font-size:12px;line-height:24.5px;color:var(--muted)}
.card .btn{display:inline-flex;align-items:center;justify-content:center;margin-top:20px;width:114px;height:40px;border-radius:3px;color:var(--white);font-size:12px;font-weight:600;text-transform:uppercase}
.card.amber{border-bottom:4px solid var(--amber)}.card.amber .btn{background:var(--amber)}
.card.lime{border-bottom:4px solid var(--lime)}.card.lime .btn{background:var(--lime)}
.card.steel{border-bottom:4px solid var(--steel)}.card.steel .btn{background:var(--steel)}

/* video */
.video-band{left:0;top:1233px;width:1200px;height:403px;background:var(--pale)}
.video{left:87px;top:1279px;width:447px;height:303px;background:linear-gradient(180deg,#b9c3cc 0%,#9a8660 55%,#e9ecef 100%)}
.video-play{left:193px;top:114px;width:62px;height:46px;border-radius:10px;background:rgba(30,30,30,.8)}
.video-bar{left:0;bottom:0;width:100%;height:27px;background:#1b1b1b}
.video-progress{left:0;top:0;width:100%;height:3px;background:#c62828}
.video-time{left:80px;top:6px;font-size:10px;color:#ddd}
.feat-head{left:579px;top:1268px;display:flex;align-items:center;gap:12px;font-family:"Montserrat",Arial,sans-serif;font-weight:700;font-size:25px;text-transform:uppercase}
.feat-head .mark{width:24px;height:24px;background:var(--ink)}
.feat-head .hl{color:var(--lime)}.feat-head .rest{color:var(--ink)}
.feat-text{left:579px;top:1312px;width:525px;font-size:12px;line-height:25.5px;color:var(--text)}
.feat-list{left:579px;top:1412px;list-style:none}
.feat-list li{display:flex;align-items:center;height:34.5px;font-size:12px;color:var(--text);white-space:nowrap}
.feat-list li::before{content:"";width:20px;height:14px;background:var(--ink);margin-right:27px}

/* testimonials */
.testi{left:0;top:1636px;width:1200px;height:299px;background:var(--lime)}
.testi-head{left:0;top:42px;width:1200px;display:flex;justify-content:center;align-items:center;gap:12px;font-family:"Montserrat",Arial,sans-serif;font-weight:700;font-size:25px;color:var(--white);text-transform:uppercase}
.testi-head .mark{width:24px;height:24px;background:var(--white)}
.testi-arrows{left:928px;top:48px;color:var(--white);font-size:14px;letter-spacing:6px}
.avatar{left:232px;top:104px;width:118px;height:118px;border-radius:50%;border:5px solid var(--white);background:linear-gradient(160deg,#6d8fb2,#3e5d7d)}
.quote-mark{color:var(--white);font-family:Georgia,serif;font-size:34px;line-height:1}
.testi-quote{left:403px;top:116px;width:540px;font-style:italic;font-size:12px;line-height:23.5px;color:var(--white)}
.testi-name{left:403px;top:206px;font-size:10px;font-weight:700;color:var(--white);text-transform:uppercase}
.testi-date{left:403px;top:225px;font-size:11px;color:var(--white)}

/* news */
.news{top:2106px;width:340px;height:121px}
.news-img{left:0;top:0;width:129px;height:121px}
.news h4{position:absolute;left:151px;top:0;font-size:14px;font-weight:600;color:var(--ink)}
.news p{position:absolute;left:151px;top:26px;width:185px;font-size:12px;line-height:22px;color:var(--muted)}
.news .meta{position:absolute;left:151px;top:102px;display:flex;align-items:center;gap:10px;font-size:10.5px;color:var(--muted)}
.stars{color:var(--amber);font-size:12px;letter-spacing:1px}
.stars .off{color:#9a9a9a}

/* footer */
.footer{left:0;top:2285px;width:1200px;height:232px;background:var(--footer);border-top:4px solid var(--lime)}
.social{left:390px;top:33px;display:flex;gap:12px}
.social span{width:60px;height:60px;border-radius:50%;border:1px solid #444;display:flex;align-items:center;justify-content:center}
.foot-nav{left:0;top:126px;width:1200px;display:flex;justify-content:center;font-size:11px;color:var(--white);text-transform:uppercase}
.foot-nav a{color:var(--white);text-decoration:none}
.foot-nav .sep{margin:0 16px}
.copy{left:0;top:170px;width:1200px;text-align:center;font-size:11px;color:#cfcfcf}
.copy a{color:#cfcfcf}
</style>
</head>
<body>

<div class="abs topline"></div>
<header class="abs header"></header>
<div class="abs brand"><span class="brand-mark"></span><span class="brand-name">Panelvance</span></div>
<nav class="abs main-nav">
  <a class="active">Home</a><a>About Us</a><a>Benefits</a><a>FAQ</a><a>Photo Gallery</a><a>Services</a><a>Kit Supply</a><a>Contact Us</a>
</nav>
<nav class="abs sub-nav">
  <a>Marlow Fen Dwellings</a><a>Designs</a><a>Residential</a><a>Granny Flats</a><a>Architectural Design</a><a>What is a SIP</a><a>Project Management</a><a>Site Assembly</a>
</nav>

<section class="abs hero" role="img" aria-label="Photo of a multi-storey timber-frame house under construction with insulated wall panels">
  <div class="abs hero-shade"></div>
  <h1 class="abs hero-title">PANELVANCE</h1>
  <p class="abs hero-text">panelvance panels can be used in residential and commercial building and are fully compliant to Australian standards.We to builders and developers specific to their needs or requirements. sips is rapidly becoming the building method of choice because of its overwhelming benefits and proven suitability.</p>
  <div class="abs hero-btn">Click here for more info</div>
  <div class="abs dots"><span></span><span class="on"></span><span></span><span></span><span></span></div>
</section>

<h2 class="abs sec-head" style="top:648px"><span class="mark"></span><span><span class="hl">Recent</span> <span class="rest">Projects</span></span></h2>
<p class="abs sec-intro" style="top:695px">panelvance panels can be used in residential and commercial building and are fully compliant to Australian standards.We&nbsp; to builders and developers specific to their needs or requirements.</p>

<article class="abs card amber" style="left:87px">
  <div class="card-img" role="img" aria-label="Photo of two builders fitting a structural insulated wall panel" style="background:linear-gradient(135deg,#c79a63,#9c7546)"></div>
  <h3>Residential</h3>
  <p>panelvance panels can be used in residential and commercial building and are fully compliant to Australian standards.</p>
  <span class="btn">Read More</span>
</article>
<article class="abs card lime" style="left:443px">
  <div class="card-img" role="img" aria-label="Photo of a two-storey house frame clad in panels under blue sky" style="background:linear-gradient(180deg,#5f8fd0 0%,#a9c2df 45%,#c99a61 100%)"></div>
  <h3>Architectural Design</h3>
  <p>panelvance panels can be used in residential and commercial building and are fully compliant to Australian standards.</p>
  <span class="btn">Read More</span>
</article>
<article class="abs card steel" style="left:797px">
  <div class="card-img" role="img" aria-label="Photo of a timber gable roof frame against a deep blue sky" style="background:linear-gradient(180deg,#2a5fae 0%,#4a78bd 45%,#9a7650 100%)"></div>
  <h3>Granny Flats</h3>
  <p>panelvance panels can be used in residential and commercial building and are fully compliant to Australian standards.</p>
  <span class="btn">Read More</span>
</article>

<section class="abs video-band"></section>
<div class="abs video" role="img" aria-label="Video still of a panel-built house shell on a snowy site">
  <svg class="abs video-play" viewBox="0 0 62 46"><polygon points="24,13 24,33 41,23" fill="#ffffff"/></svg>
  <div class="abs video-bar">
    <div class="abs video-progress"></div>
    <svg class="abs" style="left:12px;top:9px" width="10" height="12" viewBox="0 0 10 12"><polygon points="0,0 0,12 10,6" fill="#ddd"/></svg>
    <span class="abs video-time">0:00 / 3:00</span>
  </div>
</div>
<h2 class="abs feat-head"><span class="mark"></span><span><span class="hl">Featured</span> <span class="rest">Video</span></span></h2>
<p class="abs feat-text">Panelvance are designers and manufacturers of an engineered structural insulated panel and concealed structural frame building product.panelvance are designers and manufacturers of an and concealed structural frame building product.</p>
<ul class="abs feat-list">
  <li>High level of captive insulation. (warm in winter cool in summer)</li>
  <li>Very strong, light weight and durable.</li>
  <li>20 + year history of performance in cyclonic locations in WA</li>
  <li>Reduced build time (save time save money it's that easy)</li>
  <li>Energy efficient ( less energy to build and less energy to run ie lower power bills)</li>
</ul>

<section class="abs testi">
  <h2 class="abs testi-head"><span class="mark"></span><span>Our Testimonials</span></h2>
  <div class="abs testi-arrows">‹ ›</div>
  <div class="abs avatar" role="img" aria-label="Portrait photo of the client giving the testimonial"></div>
  <span class="abs quote-mark" style="left:378px;top:96px">“</span>
  <p class="abs testi-quote">panelvance are designers and manufacturers of an engineered structural insulated panel and concealed structural frame building product.panelvance are designers and manufacturers of an engineered structural insulated panel and concealed structural frame building product.</p>
  <span class="abs quote-mark" style="left:952px;top:162px">”</span>
  <div class="abs testi-name">Corin Haldane</div>
  <div class="abs testi-date">Posed on 25 Aug 2015</div>
</section>

<h2 class="abs sec-head" style="top:1965px"><span class="mark"></span><span><span class="hl">Latest</span> <span class="rest">News</span></span></h2>
<p class="abs sec-intro" style="top:2016px">panelvance panels can be used in residential and commercial building and are fully compliant to Australian standards.We&nbsp; to builders and developers specific to their needs or requirements.</p>

<article class="abs news" style="left:82px">
  <div class="abs news-img" role="img" aria-label="Photo of roof trusses being assembled on site" style="background:linear-gradient(135deg,#5d86c4,#c7793a)"></div>
  <h4>Site Assembly</h4>
  <p>panelvance panels can be used in residential and commercial builders and developers</p>
  <div class="meta"><span class="stars">★★★★<span class="off">★</span></span><span>| &nbsp;12 Reviews</span></div>
</article>
<article class="abs news" style="left:436px">
  <div class="abs news-img" role="img" aria-label="Photo of a timber-clad house nearing completion" style="background:linear-gradient(180deg,#6f9fd6,#c3935a)"></div>
  <h4>Site Assembly</h4>
  <p>panelvance panels can be used in residential and commercial builders and developers</p>
  <div class="meta"><span class="stars">★★★★<span class="off">★</span></span><span>| &nbsp;12 Reviews</span></div>
</article>
<article class="abs news" style="left:790px">
  <div class="abs news-img" role="img" aria-label="Photo of a three-storey panel house under construction" style="background:linear-gradient(180deg,#8db5dc,#d2a24e)"></div>
  <h4>Site Assembly</h4>
  <p>panelvance panels can be used in residential and commercial builders and developers</p>
  <div class="meta"><span class="stars">★★★★<span class="off">★</span></span><span>| &nbsp;12 Reviews</span></div>
</article>

<footer class="abs footer">
  <div class="abs social">
    <span></span><span></span><span></span><span></span><span></span>
    <span><svg width="18" height="14" viewBox="0 0 18 14"><rect x="1" y="1" width="16" height="12" fill="none" stroke="#ffffff" stroke-width="1.5"/><polyline points="1,1 9,8 17,1" fill="none" stroke="#ffffff" stroke-width="1.5"/></svg></span>
  </div>
  <nav class="abs foot-nav">
    <a>Home</a><span class="sep">|</span><a>About Us</a><span class="sep">|</span><a>Benefits</a><span class="sep">|</span><a>FAQ</a><span class="sep">|</span><a>Photo Gallery</a><span class="sep">|</span><a>Services</a><span class="sep">|</span><a>Kit Supply</a><span class="sep">|</span><a>Contact Us</a>
  </nav>
  <p class="abs copy">© Copyrights 2016 Perth, Australia. <a>Terms of Use</a> &nbsp;<a>Privacy Policy</a></p>
</footer>

</body>
</html>
```